Creation of a construction/bricklaying business website

Following the template format of "Halloway 7", the following content would need to be included:
1. Landing page with 3 tiles that go to their own pages.
- Landing page to include background photo and description of services offered.
2. 3 tiles to include:
a) "Contact Us For A Free Quote or Friendly Discussion" Form (middle tile)
b) Case Studies and Testimonials
c) Certifications and Professional Membership
- Design logo to be used from previous SketchNestle project. Example of logo attached below, please access full JPG files from our account.

Target Market(s)

Prospective clients seeking construction work (bricklaying speciality)

Industry/Entity Type

Residential Construction

Coding

Coded - Design and coding required

Number of Pages Required

4 page

Font styles to use
Sans Serif

Colors

Designer to choose colors to be used in the design.

Requirements
Must have
• Following the template format of "Halloway 7", the following content would need to be included:
• 1. Landing parent page with 3 tiles that go to the 3 child pages.
• - Landing page to include background photo and description of services offered.
• 2. 3 tiles to include:
• a) "Contact Us For A Free Quote or Friendly Discussion" Form (middle tile)
• b) Case Studies and Testimonials (first tile / left side)
• c) Certifications and Professional Memberships (third tile / right side) (This should include logos of the relevant organisations being displayed. Specifically GQT and the Pillar Seal GQT).
• - Design logo to be used from previous SketchNestle project. Example of logo attached below, please access full JPG files from our account.
Nice to have
• Sleek and modern feel.
• Approachable in terms of how people can contact the company for a quote.
• Traditional pictures to give credibility and comfort around choosing this company.
Should not have
• Cheesy pictures
• Over-complicated
• Simple to use
• Easy URL domain name

```html
<!DOCTYPE html>
<html lang="en">
<head>
<meta charset="utf-8">
<title>R.T. Marsh Construction Ltd</title>
<link href="https://fonts.googleapis.com/css2?family=Open+Sans:wght@400;600;700&display=swap" rel="stylesheet">
<style>
:root{
  --blue:#0d4fa6;
  --blue-dark:#0a3d82;
  --ink:#1d1d1d;
  --text:#444;
  --muted:#8a8a8a;
  --panel:#f5f5f5;
  --line:#d6d6d6;
  --footer-top:#2c2c2c;
  --footer:#232323;
  --footer-bar:#1b1b1b;
  --white:#fff;
}
*{box-sizing:border-box;margin:0;padding:0}
html,body{width:1200px;height:3468px;overflow:hidden}
body{font-family:"Open Sans",Arial,sans-serif;color:var(--text);background:var(--white);position:relative}
.abs{position:absolute}
.hero{left:0;top:0;width:1200px;height:590px;background:linear-gradient(180deg,#0d2c70 0%,#24477f 45%,#5b5450 80%,#2a2620 100%)}
.brand{font-weight:700;color:var(--white);font-size:34px;line-height:1;letter-spacing:1px}
.brand small{display:block;font-size:13px;letter-spacing:2px;margin-top:4px}
.nav{left:448px;top:38px;display:flex;gap:14px;font-size:13px;color:var(--white)}
.nav span.sep{opacity:.7}
.hero-text{left:162px;top:286px;width:670px;color:var(--white);font-size:14px;line-height:30px;font-weight:400;white-space:nowrap;letter-spacing:-.1px}
.hero-badge{left:842px;top:262px;width:62px;height:108px;background:var(--blue)}
.hero-badge-name{left:842px;top:262px;height:108px;color:var(--white);font-weight:700;font-size:32px;display:flex;align-items:center;white-space:nowrap}
.dots{left:162px;top:400px;display:flex;gap:6px}
.dots i{width:10px;height:10px;border-radius:50%;background:var(--white);opacity:.6}
.dots i:first-child{opacity:1}
.tab{width:40px}
.panel{left:0;width:1200px;background:var(--panel)}
h2{font-size:24px;font-weight:700;color:var(--ink)}
.sub{font-size:13px;color:var(--blue)}
.svc{width:210px}
.svc h3{font-size:13px;font-weight:700;color:var(--ink);margin-top:20px;padding-bottom:12px;border-bottom:2px solid var(--ink);width:44px;white-space:nowrap}
.svc p{font-size:12.5px;line-height:21px;margin-top:14px}
.btn-out{display:inline-flex;align-items:center;gap:6px;height:32px;padding:0 14px;border:1.5px solid var(--blue);color:var(--blue);font-size:12px;font-weight:600;background:var(--white);margin-top:16px}
.btn{display:flex;align-items:center;justify-content:center;background:var(--blue);color:var(--white);font-size:13px;font-weight:600}
.case-img{width:134px;height:116px;border-left:3px solid var(--blue);border-bottom:3px solid var(--blue)}
.case-body{width:260px;font-size:12px;line-height:20px}
.meta{display:flex;gap:18px;color:var(--blue);font-size:11.5px;font-weight:600;margin-bottom:10px}
.meta span{display:flex;align-items:center;gap:6px}
.case-body b{display:block;margin-top:6px;font-size:11.5px;color:var(--ink);text-decoration:underline}
.quote{left:342px;top:1681px;width:539px;height:118px;border:2px solid var(--blue);background:var(--white)}
.quote p{position:absolute;left:104px;top:24px;width:410px;font-size:13px;line-height:24px}
.field{height:36px;border:1px solid var(--line);background:var(--white);font-size:12px;color:var(--muted);padding:9px 12px}
.cert-h{font-size:14px;font-weight:700;color:var(--ink);line-height:28px;letter-spacing:.3px}
.cert-p{font-size:13px;line-height:22px}
.seal{height:64px}
.footer-top{left:0;top:3087px;width:1200px;height:92px;background:var(--footer-top);border-top:5px solid var(--blue)}
.footer{left:0;top:3179px;width:1200px;height:249px;background:var(--footer)}
.footer h4{font-size:13px;font-weight:700;color:var(--white);letter-spacing:.5px}
.footer li{list-style:none;font-size:12.5px;color:#8d8d8d;line-height:25px;display:flex;gap:10px}
.footer p{font-size:12.5px;color:#8d8d8d;line-height:22px}
.footer-bar{left:0;top:3428px;width:1200px;height:40px;background:var(--footer-bar);font-size:12.5px;color:#8d8d8d}
</style>
</head>
<body>

<section class="hero abs" role="img" aria-label="Modern apartment blocks photographed at dusk"></section>
<div class="abs brand" style="left:162px;top:34px">R.T. Marsh<small>CONSTRUCTION LTD</small></div>
<nav class="abs nav"><span>Services</span><span class="sep">/</span><span>Case Studies and Testimonials</span><span class="sep">/</span><span>Contact Us</span><span class="sep">/</span><span>Certifications and Professional Membership</span></nav>
<p class="abs hero-text">We pride ourselves on attention to detail, pride in our completed project and client satisfaction.<br>We believe in full transparency and this is reflected in the jobs we quote for you.</p>
<div class="abs hero-badge"></div>
<div class="abs hero-badge-name">R.T. MARSH</div>
<div class="abs dots"><i></i><i></i><i></i></div>

<!-- Services -->
<section class="abs panel" style="top:590px;height:555px"></section>
<svg class="abs tab" style="left:162px;top:590px" height="72" viewBox="0 0 40 72"><path d="M0 0H40V60L20 72 0 60Z" fill="var(--blue)"/></svg>
<h2 class="abs" style="left:162px;top:680px">Our Services</h2>
<p class="abs sub" style="left:162px;top:718px">R.T. Marsh Construction Ltd is a construction company that has expertise and experience</p>

<div class="abs svc" style="left:162px;top:802px">
  <svg width="56" height="58" viewBox="0 0 56 58" fill="var(--blue)"><rect x="10" y="4" width="24" height="54"/><rect x="34" y="20" width="14" height="38"/><g fill="var(--panel)"><rect x="15" y="10" width="4" height="5"/><rect x="25" y="10" width="4" height="5"/><rect x="15" y="21" width="4" height="5"/><rect x="25" y="21" width="4" height="5"/><rect x="15" y="32" width="4" height="5"/><rect x="25" y="32" width="4" height="5"/><rect x="39" y="27" width="4" height="5"/><rect x="39" y="38" width="4" height="5"/><rect x="19" y="46" width="6" height="12"/></g><rect x="2" y="56" width="52" height="2"/></svg>
  <h3>EXTENSIONS</h3>
  <p>We pride ourselves on attention to detail, pride in our completed project and client satisfaction</p>
  <span class="btn-out">Read More →</span>
</div>
<div class="abs svc" style="left:391px;top:802px">
  <svg width="70" height="58" viewBox="0 0 70 58" fill="var(--blue)"><path d="M35 2 68 30H60V58H10V30H2Z"/><rect x="29" y="38" width="12" height="20" fill="var(--panel)"/><rect x="17" y="34" width="8" height="8" fill="var(--panel)"/><rect x="45" y="34" width="8" height="8" fill="var(--panel)"/></svg>
  <h3>NEW BUILD / NEW HOUSES</h3>
  <p>We pride ourselves on attention to detail, pride in our completed project and client satisfaction</p>
  <span class="btn-out">Read More →</span>
</div>
<div class="abs svc" style="left:620px;top:802px">
  <svg width="70" height="58" viewBox="0 0 70 58" fill="var(--blue)"><g><rect x="2" y="4" width="20" height="10"/><rect x="25" y="4" width="20" height="10"/><rect x="48" y="4" width="20" height="10"/><rect x="2" y="17" width="9" height="10"/><rect x="14" y="17" width="20" height="10"/><rect x="37" y="17" width="20" height="10"/><rect x="60" y="17" width="8" height="10"/><rect x="2" y="30" width="20" height="10"/><rect x="25" y="30" width="20" height="10"/><rect x="48" y="30" width="20" height="10"/><rect x="2" y="43" width="9" height="10"/><rect x="14" y="43" width="20" height="10"/><rect x="37" y="43" width="20" height="10"/><rect x="60" y="43" width="8" height="10"/></g></svg>
  <h3>GARDEN WALLS</h3>
  <p>We pride ourselves on attention to detail, pride in our completed project and client satisfaction</p>
  <span class="btn-out">Read More →</span>
</div>
<div class="abs svc" style="left:849px;top:802px">
  <svg width="70" height="58" viewBox="0 0 70 58" fill="var(--blue)"><rect x="2" y="22" width="20" height="10"/><rect x="25" y="22" width="20" height="10"/><rect x="2" y="35" width="9" height="10"/><rect x="14" y="35" width="20" height="10"/><rect x="37" y="35" width="20" height="10"/><rect x="2" y="48" width="20" height="10"/><rect x="25" y="48" width="20" height="10"/><rect x="48" y="48" width="18" height="10"/><path d="M40 18 58 4 66 10 48 24Z"/><rect x="60" y="0" width="4" height="10" transform="rotate(40 62 5)"/></svg>
  <h3>BRICKWORK</h3>
  <p>We pride ourselves on attention to detail, pride in our completed project and client satisfaction</p>
  <span class="btn-out">Read More →</span>
</div>
<div class="abs btn" style="left:509px;top:1057px;width:182px;height:37px">View More Services</div>

<!-- Case studies -->
<svg class="abs" style="left:162px;top:1145px" width="40" height="80" viewBox="0 0 40 80"><path d="M0 0H40L20 30Z" fill="var(--blue)"/><rect x="18.5" y="28" width="3" height="52" fill="var(--blue)"/></svg>
<h2 class="abs" style="left:162px;top:1254px">Case Studies</h2>

<div class="abs case-img" style="left:162px;top:1322px;background:linear-gradient(180deg,#cfe1f2,#9db5c9 55%,#6b8f4a)" role="img" aria-label="Modern residential block with trees in front"></div>
<div class="abs case-body" style="left:319px;top:1322px">
  <div class="meta"><span>▣ 6 August 2018</span><span>▢ Comment</span></div>
  Lorem Ipsum is simply dummy text of the printing and typesetting industry. has been the industry's standard dummy text...
  <b>READ MORE</b>
</div>
<div class="abs case-img" style="left:636px;top:1322px;background:linear-gradient(180deg,#2a55b0,#5b7dc9 50%,#c58a55)" role="img" aria-label="Contemporary apartment building lit at dusk"></div>
<div class="abs case-body" style="left:786px;top:1322px">
  <div class="meta"><span>▣ 6 August 2018</span><span>▢ Comment</span></div>
  Lorem Ipsum is simply dummy text of the printing and typesetting industry. has been the industry's standard dummy text...
  <b>READ MORE</b>
</div>
<div class="abs btn" style="left:509px;top:1487px;width:182px;height:37px">View More Case Studies</div>

<div class="abs" style="left:0;top:1574px;width:1200px;height:3px;background:#e6e6e6"></div>

<!-- Testimonials -->
<h2 class="abs" style="left:162px;top:1618px">Testimonials</h2>
<div class="abs" style="left:162px;top:1711px;width:3px;height:277px;background:var(--blue)"></div>
<svg class="abs" style="left:290px;top:1736px" width="24" height="24" viewBox="0 0 24 24"><circle cx="12" cy="12" r="10" fill="none" stroke="#555" stroke-width="1.5"/><path d="M14 7 9 12 14 17" fill="none" stroke="#555" stroke-width="2"/></svg>
<svg class="abs" style="left:892px;top:1736px" width="24" height="24" viewBox="0 0 24 24"><circle cx="12" cy="12" r="10" fill="none" stroke="#555" stroke-width="1.5"/><path d="M10 7 15 12 10 17" fill="none" stroke="#555" stroke-width="2"/></svg>
<div class="abs quote">
  <svg class="abs" style="left:28px;top:26px" width="56" height="46" viewBox="0 0 56 46" fill="#e1e1e1"><path d="M0 0H24V24L14 46H4L12 24H0Z"/><path d="M30 0H54V24L44 46H34L42 24H30Z"/></svg>
  <div class="abs" style="left:90px;top:20px;width:1px;height:76px;background:var(--line)"></div>
  <p>We pride ourselves on attention to detail, pride in our completed project and client satisfaction. We believe in full transparency and this is reflected in the jobs we quote for you....</p>
</div>
<svg class="abs" style="left:585px;top:1797px" width="30" height="16" viewBox="0 0 30 16"><path d="M0 0 15 15 30 0" fill="var(--white)" stroke="var(--blue)" stroke-width="2"/></svg>
<div class="abs" style="left:567px;top:1827px;width:64px;height:64px;border-radius:50%;background:linear-gradient(180deg,#d8d2cc,#6c625c)" role="img" aria-label="Client portrait"></div>
<div class="abs" style="left:500px;top:1904px;width:200px;text-align:center;font-size:12px;font-weight:700;color:var(--ink)">HELENA MORROW</div>
<div class="abs" style="left:500px;top:1923px;width:200px;text-align:center;font-size:11.5px">6-Aug-2018</div>

<!-- Contact -->
<section class="abs panel" style="top:2007px;height:425px"></section>
<svg class="abs" style="left:162px;top:1984px" width="40" height="108" viewBox="0 0 40 108"><rect x="18.5" y="0" width="3" height="30" fill="var(--blue)"/><path d="M20 24 40 36V108H0V36Z" fill="var(--blue)"/></svg>
<h2 class="abs" style="left:162px;top:2115px">Contact Us For A Free Quote or Friendly Discussion</h2>
<div class="abs field" style="left:162px;top:2185px;width:208px">Name :</div>
<div class="abs field" style="left:379px;top:2185px;width:206px">E-mail :</div>
<div class="abs field" style="left:592px;top:2185px;width:206px">Phone :</div>
<div class="abs field" style="left:807px;top:2185px;width:206px">Post Code :</div>
<div class="abs field" style="left:162px;top:2226px;width:874px;height:68px">Description of the job required</div>
<div class="abs btn" style="left:546px;top:2324px;width:111px;height:34px">Submit</div>

<!-- Certifications -->
<svg class="abs" style="left:162px;top:2432px" width="40" height="100" viewBox="0 0 40 100"><rect x="18.5" y="0" width="3" height="60" fill="var(--blue)"/><path d="M0 56H40L20 88Z" fill="var(--blue)"/><rect x="18.5" y="86" width="3" height="14" fill="var(--blue)"/></svg>
<h2 class="abs" style="left:162px;top:2545px">Certifications and Professional Memberships</h2>
<div class="abs cert-h" style="left:162px;top:2617px;width:520px">R.T. MARSH CONSTRUCTION IS A REGISTERED COMPANY WITH THE GUILD OF QUALITY TRADESMEN</div>
<p class="abs cert-p" style="left:162px;top:2684px;width:500px">The GQT has a strict membership criteria and dispute resolution service which gives our clients the confidence to entrust their residential building requirements with R.T. Marsh Construction.<br>To be a member of the GQT, a company must be inspected by GQT inspectors as well as Regional Build Inspectors. GQT and RBI will be present onsite to inspect our work as well as conducting interviews with the owner of R.T. Marsh Construction and our employees.</p>
<div class="abs btn" style="left:162px;top:2862px;width:111px;height:37px">Read More</div>
<div class="abs seal" style="left:162px;top:2937px;width:138px;background:#c9252c" role="img" aria-label="GQT membership badge"></div>
<div class="abs seal" style="left:319px;top:2937px;width:132px;background:#b51f2a;border:3px solid #1b3f8a" role="img" aria-label="Pillar Seal GQT badge"></div>
<div class="abs seal" style="left:467px;top:2932px;width:74px;height:72px;background:#f08a1c" role="img" aria-label="Local building control badge"></div>
<div class="abs seal" style="left:555px;top:2950px;width:122px;height:34px;border-radius:17px;background:#e23a3a" role="img" aria-label="Detection services badge"></div>
<div class="abs" style="left:729px;top:2634px;width:304px;height:372px;background:var(--blue)"></div>
<div class="abs" style="left:705px;top:2624px;width:312px;height:370px;background:linear-gradient(180deg,#5d9be0 0%,#a9c9ea 35%,#e8edf1 60%,#9aa7a2 100%)" role="img" aria-label="White modern apartment tower against a blue sky"></div>

<!-- Footer -->
<footer>
<div class="abs footer-top">
  <div class="abs brand" style="left:162px;top:24px;color:var(--blue);font-size:30px">R.T. Marsh<small style="color:#bdbdbd;font-size:11px">CONSTRUCTION LTD</small></div>
  <svg class="abs" style="left:899px;top:34px" width="122" height="28" viewBox="0 0 122 28" fill="#4a4a4a"><circle cx="14" cy="14" r="13"/><circle cx="45" cy="14" r="13"/><circle cx="76" cy="14" r="13"/><circle cx="107" cy="14" r="13"/></svg>
</div>
<div class="abs footer">
  <h4 class="abs" style="left:162px;top:52px">CONTACT US</h4>
  <ul class="abs" style="left:162px;top:92px;width:190px">
    <li>☏&nbsp; +1098765432</li>
    <li style="line-height:20px;margin:6px 0">⚲&nbsp; Lorem Ipsum is dummy text industry.</li>
    <li>✉&nbsp; hello@rtmarshbuild.com</li>
  </ul>
  <h4 class="abs" style="left:388px;top:52px">OUR SERVICES</h4>
  <ul class="abs" style="left:388px;top:92px">
    <li>→ Extensions</li><li>→ New build / New houses</li><li>→ Garden walls</li><li>→ Plastering</li><li>→ Brickwork</li>
  </ul>
  <h4 class="abs" style="left:580px;top:52px">INFORMATION</h4>
  <p class="abs" style="left:580px;top:92px;width:200px">We pride ourselves on attention to detail, pride in our completed project &amp; client satisfaction</p>
  <p class="abs" style="left:580px;top:166px">Read More →</p>
  <p class="abs" style="left:816px;top:92px;width:240px">© Copyright 2018 R.T. Marsh Construction. All Rights Reserved.</p>
</div>
<div class="abs footer-bar">
  <span class="abs" style="left:158px;top:11px">Services &nbsp; / &nbsp; Case Studies and Testimonials &nbsp; / &nbsp; Contact Us &nbsp; / &nbsp; Certifications and Professional Memberships</span>
  <span class="abs" style="left:956px;top:11px">Privacy Policy</span>
</div>
</footer>

</body>
</html>
```